Maple Lantern Productions web site

I need to build a website for a new company I am launching next month. Maple Lantern Productions is a company based in New England that provides sound, lighting, and audio visual services to weddings, corporate, and any other cusomer base looking for quality service for a fair price. Looking for somebody to do a full site not just the image files. I am looking to keep the colors of my logo (orange and black) and possibly grey and white. I am looking to build my site very similar to brightvaleevents.example, which is owned by a friend of mine. I like how he has the big pictures that load in to the site and the basic menu items. I'll need a gallery of photos. The designs should communicate quality, value and trust.
My website address is maplelanternco.example.
Updates

Hi and thanks to everyone for posting such great ideas for our new design.I have some items that I'd like to ask you all to focus on in your revisions.I like how http://www.brightvaleevents.example/ website has five or six high res pictures that change in a slideshow format with a caption that loads in for each one for the different types of services. Try and capture pics like these and with teh same headings as he has. The basic menu designs have been interesting.I am more fond of the menus that are more white with some orange as I dont want it to be too dark. I'm curious to see how your galleries will work and if i'll be able to edit the pages myself? I have some more info on the company for you to fill in:website address is ciderhouseco.comemail: info@ciderhouseco.comaddress: Maple Lantern Productions57 Littlefield StreetAvon, MA 02417"New England's finest DJ's, lighting and sound, video and more. Creating memories one perfect event at a time."Put this under the loading pictures as a tagline.About Cider HouseCider House Productions is a collection of New England's finest talent, ready to make your next event the one you've dreamed of. We have the skills and expertise to deliver your vision of your perfect event. From elegant weddings to themed mitzvah's, corporate av, videography and detail lighting, we offer all of the elements to make your event a success. Added Wednesday, March 1, 2017

Designer's Please also make sure that your design flows well on any device it is being viewed on as well. Thanks. Added Wednesday, March 1, 2017

Project Deadline Extended Reason: Hello designerThank you all very much for your hard work on our project. Im sorry but i need to extend the date of my project. Our parent conpany Rook Nine Prodactions sponsors Bay Youth Assemblies and we are currently at their leadership conference on the Cape. I will be back in on Monday and with your help will get this finished by Thursday the 16th. Thanks Added Thursday, March 9, 2017

Project Deadline Extended Reason: One of the designers is not responding so I now have to make revisions with other designers. I hope to get this website done over the weekends so please get your revisions as soon as possible. Thank you. I am also upgrading the budget another $75 to hopefully get some more interest on my project. Added Wednesday, March 15, 2017

Target Market(s)

Wedding - Corporate -

Industry/Entity Type

It Company

Coding

Coded - Design and coding required

Number of Pages Required

5+ page

Font styles to use
Sans Serif

Requirements
Must have
• Photo Gallery - I want to be able to edit it myself
Nice to have
• I like the look of my friends website brightvaleevents.example

```html
<!DOCTYPE html>
<html lang="en">
<head>
<meta charset="utf-8">
<title>Maple Lantern Productions</title>
<link href="https://fonts.googleapis.com/css2?family=Open+Sans:ital,wght@0,300;0,400;0,600;0,700;0,800;1,400&display=swap" rel="stylesheet">
<style>
:root{
  --orange:#f26d21;
  --ink:#222222;
  --text:#555555;
  --muted:#888888;
  --light:#f4f4f4;
  --card:#ececec;
  --grey-bar:#a9a9a9;
  --dark:#2a2a2a;
  --darker:#1c1c1c;
  --white:#ffffff;
}
*{margin:0;padding:0;box-sizing:border-box}
html,body{width:1200px;height:3666px;overflow:hidden}
body{font-family:"Open Sans",Arial,sans-serif;color:var(--text);background:var(--white);position:relative}

/* header */
.site-header{position:absolute;left:0;top:0;width:1200px;height:117px;background:var(--white)}
.brand{position:absolute;left:134px;top:22px;display:flex;align-items:center;gap:12px}
.brand-mark{width:64px;height:64px;border-radius:50%;background:var(--orange)}
.brand-name{font-weight:800;font-size:24px;line-height:25px;color:var(--ink);letter-spacing:.5px}
.brand-name small{display:block;font-size:14px;letter-spacing:5px;font-weight:800}
.top-contact{position:absolute;right:134px;top:28px;display:flex;gap:26px;font-size:11px;color:var(--muted);align-items:center}
.top-contact b{font-size:14px;color:var(--ink);font-weight:700;margin-left:4px}
.top-contact svg{vertical-align:middle;margin-right:4px}
.main-nav{position:absolute;right:134px;top:64px;display:flex;gap:6px}
.main-nav a{font-size:12px;color:var(--ink);text-decoration:none;padding:7px 12px;border:1px solid transparent}
.main-nav a.active{border-color:var(--orange);color:var(--orange);font-weight:600}

/* hero */
.hero{position:absolute;left:0;top:117px;width:1200px;height:513px;
  background:
    radial-gradient(ellipse 180px 120px at 43% 6%,rgba(196,150,120,.55),transparent 70%),
    radial-gradient(ellipse 160px 110px at 64% 40%,rgba(170,130,110,.45),transparent 70%),
    radial-gradient(circle 230px at 17% 62%,rgba(95,85,100,.55),transparent 72%),
    radial-gradient(circle 250px at 86% 58%,rgba(90,80,95,.5),transparent 72%),
    radial-gradient(ellipse 260px 140px at 50% 78%,rgba(40,95,100,.45),transparent 70%),
    linear-gradient(180deg,#241a22 0%,#1a1319 55%,#0d0a0e 100%)}
.hero::before{content:"";position:absolute;inset:0;background:linear-gradient(90deg,rgba(0,0,0,.45) 0%,rgba(0,0,0,.1) 55%,rgba(0,0,0,0) 100%)}
.hero-title{position:absolute;left:130px;top:146px;font-size:48px;font-weight:800;color:var(--white);letter-spacing:.5px}
.hero-copy{position:absolute;left:130px;top:218px;width:520px;font-size:16px;line-height:28px;color:var(--white)}
.hero-btn{position:absolute;left:130px;top:316px;padding:11px 18px;border:2px solid var(--white);color:var(--white);font-size:13px;font-weight:700}
.hero-dots{position:absolute;left:985px;top:440px;display:flex;gap:10px}
.hero-dots i{width:10px;height:10px;border-radius:50%;border:1px solid #ccc;display:block}
.hero-dots i.on{background:var(--orange);border-color:var(--orange)}

/* section bands */
.band{position:absolute;left:0;width:1200px;height:86px;background:var(--orange);color:var(--white);text-align:center;font-size:30px;font-weight:300;line-height:86px;letter-spacing:.5px;z-index:2}
.band b{font-weight:700}
.band::after{content:"";position:absolute;left:582px;bottom:-18px;border-left:18px solid transparent;border-right:18px solid transparent;border-top:18px solid var(--orange)}

/* services */
.service{position:absolute;width:453px;height:196px;background:var(--card)}
.service .photo{position:absolute;top:0;width:190px;height:190px;border-radius:50%;border:5px solid var(--white);box-shadow:0 2px 6px rgba(0,0,0,.15)}
.service.left .photo{left:-8px}
.service.right .photo{right:-8px}
.service .body{position:absolute;top:32px;width:210px}
.service.left .body{left:212px}
.service.right .body{left:28px}
.service h3{font-size:14px;font-weight:400;color:var(--ink);margin-bottom:8px}
.service h3 b{font-weight:700}
.service p{font-size:11px;line-height:18px;color:var(--muted)}
.service .more{display:inline-block;margin-top:12px;background:var(--orange);color:var(--white);font-size:10px;padding:7px 12px}

/* supporters */
.divider{position:absolute;left:0;top:1295px;width:1200px;height:1px;background:#e5e5e5}
.supporters-title{position:absolute;left:0;top:1370px;width:1200px;text-align:center;font-size:17px;font-weight:400;color:var(--ink)}
.supporters-title b{font-weight:700}
.intro{position:absolute;left:160px;width:880px;text-align:center;font-size:12px;line-height:22px;font-style:italic;color:var(--muted)}
.intro em{color:var(--orange)}
.supporter-row{position:absolute;left:140px;top:1490px;width:920px;display:flex;justify-content:space-between;align-items:center}
.supporter-row span{display:block;background:#c4c4c4}

/* about */
.about{position:absolute;left:0;top:1789px;width:1200px;height:521px;
  background:
    radial-gradient(circle 90px at 12% 20%,rgba(230,230,220,.35),transparent 70%),
    radial-gradient(circle 120px at 30% 8%,rgba(220,220,210,.3),transparent 70%),
    radial-gradient(circle 110px at 58% 14%,rgba(235,235,225,.32),transparent 70%),
    radial-gradient(circle 100px at 80% 22%,rgba(225,225,215,.3),transparent 70%),
    radial-gradient(circle 130px at 95% 6%,rgba(240,240,230,.28),transparent 70%),
    radial-gradient(ellipse 600px 180px at 50% 100%,rgba(10,10,10,.6),transparent 80%),
    linear-gradient(180deg,#3c3c3c 0%,#2b2b2b 50%,#1e1e1e 100%)}
.about::before{content:"";position:absolute;inset:0;background:rgba(0,0,0,.25)}
.about-copy{position:absolute;left:160px;top:30px;width:880px;text-align:center;font-size:12px;line-height:24px;color:#e2e2e2}
.member{position:absolute;top:158px;width:222px;height:276px;background:var(--white);text-align:center}
.member .avatar{position:absolute;left:51px;top:-42px;width:120px;height:120px;border-radius:50%;border:4px solid var(--white)}
.member h4{margin-top:120px;font-size:14px;font-weight:400;color:var(--orange)}
.member .role{font-size:9px;color:var(--ink);margin-top:6px;letter-spacing:.5px}
.member p{font-size:11px;line-height:18px;color:var(--text);margin:12px 22px 0}

/* testimonials */
.quote{position:absolute;top:2428px;width:450px}
.quote p{font-size:11.5px;line-height:20px;color:var(--muted)}
.quote p::before{content:"\201C";font-size:26px;color:#bbb;vertical-align:-9px;margin-right:2px}
.quote .author{position:absolute;top:104px;left:0;display:flex;align-items:center;gap:12px}
.quote .face{width:66px;height:66px;border-radius:50%}
.quote .name{font-size:11px;color:var(--ink)}
.stars{display:flex;gap:2px;margin-top:6px}
.stars i{width:15px;height:13px;background:var(--orange);display:block}
.quote-sep{position:absolute;left:599px;top:2420px;width:1px;height:230px;background:#e3e3e3}

/* availability */
.availability{position:absolute;left:0;top:2725px;width:1200px;height:122px;background:var(--grey-bar)}
.availability .label{position:absolute;left:130px;top:48px;color:var(--white);font-size:18px}
.availability .label b{font-weight:700}
.select{position:absolute;top:44px;width:190px;height:34px;background:var(--white);font-size:11px;color:var(--muted);padding:9px 10px}
.select::after{content:"\25B4\A\25BE";white-space:pre;position:absolute;right:8px;top:6px;font-size:8px;line-height:9px;color:#666}
.check-btn{position:absolute;left:933px;top:44px;width:133px;height:34px;background:var(--orange);color:var(--white);font-size:11px;font-weight:700;text-align:center;line-height:34px}

/* gallery */
.gallery{position:absolute;left:0;top:2933px;width:1200px;height:525px;background:var(--light)}
.shot{position:absolute;border:2px solid var(--white);box-shadow:0 1px 4px rgba(0,0,0,.15)}

/* footer */
.site-footer{position:absolute;left:0;top:3458px;width:1200px;height:169px;background:var(--dark);border-top:4px solid var(--orange);color:#cccccc}
.site-footer h5{position:absolute;top:22px;font-size:16px;font-weight:400;color:var(--white)}
.foot-item{position:absolute;font-size:11px;line-height:18px;display:flex;gap:8px}
.foot-item i{width:12px;height:12px;background:var(--orange);display:block;margin-top:3px}
.news-input{position:absolute;left:530px;top:66px;width:200px;height:34px;background:var(--white);font-size:11px;color:var(--muted);padding:10px}
.news-btn{position:absolute;left:734px;top:66px;width:86px;height:34px;background:var(--orange);color:var(--white);font-size:10px;font-weight:700;text-align:center;line-height:34px}
.socials{position:absolute;left:905px;top:66px;display:flex;gap:10px}
.socials i{width:32px;height:32px;border-radius:50%;border:2px solid #cccccc;display:block}
.copyright{position:absolute;left:0;top:3627px;width:1200px;height:39px;background:var(--darker);color:#aaaaaa;font-size:11px;text-align:center;line-height:39px}
</style>
</head>
<body>

<header class="site-header">
  <div class="brand">
    <span class="brand-mark"></span>
    <div class="brand-name">MAPLE LANTERN<small>PRODUCTIONS</small></div>
  </div>
  <div class="top-contact">
    <span><svg width="12" height="12" viewBox="0 0 24 24"><path fill="#f26d21" d="M6.6 10.8a15 15 0 0 0 6.6 6.6l2.2-2.2c.3-.3.7-.4 1-.2 1.1.4 2.3.6 3.6.6.6 0 1 .4 1 1V20c0 .6-.4 1-1 1A17 17 0 0 1 3 4c0-.6.4-1 1-1h3.5c.6 0 1 .4 1 1 0 1.3.2 2.5.6 3.6.1.3 0 .7-.2 1z"/></svg>PHONE : <b>(555) 014-2290</b></span>
    <span><svg width="14" height="11" viewBox="0 0 24 18"><rect x="1" y="1" width="22" height="16" fill="none" stroke="#f26d21" stroke-width="2"/><path d="M1 1l11 9 11-9" fill="none" stroke="#f26d21" stroke-width="2"/></svg>MAIL : <b>info@maplelanternco.example</b></span>
  </div>
  <nav class="main-nav">
    <a class="active">HOME</a><a>ABOUT US</a><a>SERVICES</a><a>TESTIMONIALS</a><a>GALLERY</a><a>CONTACT US</a>
  </nav>
</header>

<section class="hero" role="img" aria-label="Photo of a DJ's hands on turntables and a mixer">
  <h1 class="hero-title">SOUND &amp; ENTERTAINMENT</h1>
  <p class="hero-copy">Nam libero tempore, cum soluta nobis est eligendi optio cumque nihil impedit quo minus id quod maxime placeat facere...</p>
  <span class="hero-btn">GET START TODAY</span>
  <div class="hero-dots"><i></i><i></i><i class="on"></i><i></i></div>
</section>

<h2 class="band" style="top:630px">OUR <b>SERVICES</b></h2>

<article class="service left" style="left:134px;top:782px">
  <div class="photo" role="img" aria-label="Photo of hands on a DJ controller" style="background:radial-gradient(circle at 40% 30%,#e0a98c 0%,rgba(224,169,140,0) 30%),radial-gradient(circle at 70% 75%,#d44a8a 0%,rgba(212,74,138,0) 35%),linear-gradient(135deg,#3d57a0,#1b2346 70%,#0f1326)"></div>
  <div class="body"><h3><b>SOUND</b> SERVICES</h3><p>Adipisci velit, sed quia non numquam modi tempora incidunt ut labore dolore magnam aliquam quaerat enim...</p><span class="more">VIEW MORE INFO</span></div>
</article>
<article class="service right" style="left:611px;top:782px">
  <div class="photo" role="img" aria-label="Photo of a lit banquet hall with chandelier" style="background:radial-gradient(circle at 45% 30%,#fff4d6 0%,rgba(255,244,214,0) 35%),radial-gradient(ellipse at 50% 85%,#f2e6d2 0%,rgba(242,230,210,0) 45%),linear-gradient(160deg,#e6c894,#b48a50 60%,#7a5a32)"></div>
  <div class="body"><h3><b>LIGHTING</b> SERVICES</h3><p>Adipisci velit, sed quia non numquam modi tempora incidunt ut labore dolore magnam aliquam quaerat enim...</p><span class="more">VIEW MORE INFO</span></div>
</article>
<article class="service left" style="left:134px;top:1014px">
  <div class="photo" role="img" aria-label="Photo of a mixing desk with faders" style="background:radial-gradient(circle at 60% 40%,#f0a54a 0%,rgba(240,165,74,0) 40%),radial-gradient(circle at 25% 70%,#c8733a 0%,rgba(200,115,58,0) 35%),linear-gradient(135deg,#6e4624,#2a180c 75%)"></div>
  <div class="body"><h3><b>AUDIO VISUAL</b> SERVICES</h3><p>Adipisci velit, sed quia non numquam modi tempora incidunt ut labore dolore magnam aliquam quaerat enim...</p><span class="more">VIEW MORE INFO</span></div>
</article>
<article class="service right" style="left:611px;top:1014px">
  <div class="photo" role="img" aria-label="Photo of a wedding couple" style="background:radial-gradient(ellipse at 35% 65%,#fafafa 0%,rgba(250,250,250,0) 40%),radial-gradient(circle at 70% 55%,#3a3535 0%,rgba(58,53,53,0) 35%),radial-gradient(circle at 60% 85%,#c94a4a 0%,rgba(201,74,74,0) 22%),linear-gradient(160deg,#d8d2c8,#9c9284 70%)"></div>
  <div class="body"><h3><b>WEDDINGS</b> SERVICES</h3><p>Adipisci velit, sed quia non numquam modi tempora incidunt ut labore dolore magnam aliquam quaerat enim...</p><span class="more">VIEW MORE INFO</span></div>
</article>

<div class="divider"></div>
<h2 class="supporters-title">OUR <b>SUPPORTERS</b></h2>
<p class="intro" style="top:1402px">Adipiscing elit, sed do eiusmod tempor incididunt ut labore et dolore magna aliqua. Ut <em>enim ad minim veniam, quis</em> nostrud exercitation ullamco laboris nisi ut <em>aliquip ex ea commodo</em> consequat. Duis aute irure dolor in reprehenderit in voluptate velit esse...</p>
<div class="supporter-row">
  <span style="width:80px;height:24px"></span>
  <span style="width:70px;height:44px;border-radius:6px"></span>
  <span style="width:96px;height:24px"></span>
  <span style="width:146px;height:22px"></span>
  <span style="width:70px;height:70px;border-radius:50%"></span>
  <span style="width:106px;height:24px"></span>
  <span style="width:80px;height:60px"></span>
  <span style="width:100px;height:24px"></span>
</div>
<p class="intro" style="top:1590px">Adipiscing elit, sed do eiusmod tempor incididunt ut labore et dolore magna aliqua. Ut <em>enim ad minim veniam, quis</em> nostrud exercitation ullamco laboris nisi ut <em>aliquip ex ea commodo</em> consequat. Duis aute irure dolor in reprehenderit in voluptate velit esse...</p>

<h2 class="band" style="top:1706px">ABOUT <b>US</b></h2>
<section class="about" role="img" aria-label="Photo of a concert crowd under stage lights">
  <p class="about-copy">Nam libero tempore, cum soluta nobis est eligendi optio cumque nihil impedit quo minus id quod maxime placeat facere possimus, omnis voluptas assumenda est, omnis dolor repellendus. Temporibus autem quibusdam et aut officiis debitis aut rerum necessitatibus saepe eveniet ut et voluptates repudiandae sint molestiae non recusandae. Itaque earum rerum hic tenetur a sapiente delectus...</p>
  <div class="member" style="left:132px"><div class="avatar" role="img" aria-label="Team member portrait" style="background:radial-gradient(circle at 50% 55%,#c99a80 0%,rgba(201,154,128,0) 45%),linear-gradient(#8e9aa8,#5c6672)"></div><h4>Marla Quinby</h4><div class="role">VELL ILL MC</div><p>Assumenda estrepellis Temporibus autem quibusdam et aut officiis debitis aut rerum...</p></div>
  <div class="member" style="left:370px"><div class="avatar" role="img" aria-label="Team member portrait" style="background:radial-gradient(circle at 50% 55%,#d9a98e 0%,rgba(217,169,142,0) 45%),linear-gradient(#a07a5a,#5e4432)"></div><h4>Marla Quinby</h4><div class="role">VELL ILL MC</div><p>Assumenda estrepellis Temporibus autem quibusdam et aut officiis debitis aut rerum...</p></div>
  <div class="member" style="left:608px"><div class="avatar" role="img" aria-label="Team member portrait" style="background:radial-gradient(circle at 50% 60%,#d4a58a 0%,rgba(212,165,138,0) 42%),linear-gradient(#4a4a4e,#7a7f88)"></div><h4>Marla Quinby</h4><div class="role">VELL ILL MC</div><p>Assumenda estrepellis Temporibus autem quibusdam et aut officiis debitis aut rerum...</p></div>
  <div class="member" style="left:846px"><div class="avatar" role="img" aria-label="Team member portrait" style="background:radial-gradient(circle at 50% 55%,#e0b8a0 0%,rgba(224,184,160,0) 45%),linear-gradient(#b9c4cf,#8a96a2)"></div><h4>Marla Quinby</h4><div class="role">VELL ILL MC</div><p>Assumenda estrepellis Temporibus autem quibusdam et aut officiis debitis aut rerum...</p></div>
</section>

<h2 class="band" style="top:2310px">OUR <b>TESTIMONIALS</b></h2>
<blockquote class="quote" style="left:132px">
  <p>Theo knows exactly how to accomplish and complete experienced, professional, and knows how it all works. In my case, with Harbor Trust, he had to represent my interest yet get it all done in the best way...</p>
  <div class="author"><div class="face" role="img" aria-label="Client portrait" style="background:radial-gradient(circle at 50% 55%,#d2a488 0%,rgba(210,164,136,0) 45%),linear-gradient(#e8e8e8,#b8b8b8)"></div><div><div class="name">-THEO VANDERMEER</div><div class="stars"><i></i><i></i><i></i><i></i><i></i></div></div></div>
</blockquote>
<div class="quote-sep"></div>
<blockquote class="quote" style="left:638px">
  <p>Theo knows exactly how to accomplish and complete experienced, professional, and knows how it all works. In my case, with Harbor Trust, he had to represent my interest yet get it all done in the best way...</p>
  <div class="author"><div class="face" role="img" aria-label="Client portrait" style="background:radial-gradient(circle at 50% 55%,#e4bca2 0%,rgba(228,188,162,0) 45%),linear-gradient(#c9a070,#8a6540)"></div><div><div class="name">-THEO VANDERMEER</div><div class="stars"><i></i><i></i><i></i><i></i><i></i></div></div></div>
</blockquote>

<section class="availability">
  <div class="label">CHECK <b>AVAILABILITY :</b></div>
  <div class="select" style="left:338px">Month</div>
  <div class="select" style="left:536px">Day</div>
  <div class="select" style="left:734px">Year</div>
  <div class="check-btn">CLICK TO CHECK</div>
</section>

<section class="gallery">
  <div class="shot" role="img" aria-label="Photo of a decorated wedding reception hall" style="left:139px;top:68px;width:357px;height:367px;background:radial-gradient(ellipse 160px 60px at 50% 42%,rgba(255,240,250,.9),transparent 70%),radial-gradient(ellipse 200px 80px at 50% 60%,rgba(245,235,240,.6),transparent 70%),linear-gradient(180deg,#3a1e2e 0%,#c77fb0 25%,#e6b8d0 45%,#8a5a48 65%,#b8733a 80%,#5a3218 100%)"></div>
  <div class="shot" role="img" aria-label="Photo of a couple at a candlelit dinner" style="left:516px;top:68px;width:261px;height:181px;background:radial-gradient(circle 60px at 45% 35%,rgba(210,160,130,.7),transparent 70%),radial-gradient(ellipse 120px 40px at 50% 85%,rgba(240,180,90,.6),transparent 70%),linear-gradient(135deg,#3a2a30,#140e12)"></div>
  <div class="shot" role="img" aria-label="Photo of friends celebrating at a party" style="left:797px;top:68px;width:261px;height:181px;background:radial-gradient(circle 50px at 30% 45%,rgba(220,170,130,.75),transparent 70%),radial-gradient(circle 50px at 65% 40%,rgba(225,175,135,.7),transparent 70%),radial-gradient(circle 70px at 85% 20%,rgba(240,200,90,.6),transparent 70%),linear-gradient(135deg,#6a4a28,#2a1a10)"></div>
  <div class="shot" role="img" aria-label="Photo of a DJ at a mixing console" style="left:516px;top:276px;width:168px;height:154px;background:radial-gradient(circle 40px at 50% 35%,rgba(200,150,120,.6),transparent 70%),radial-gradient(ellipse 80px 30px at 50% 80%,rgba(90,140,170,.5),transparent 70%),linear-gradient(135deg,#3a2a22,#120e0c)"></div>
  <div class="shot" role="img" aria-label="Photo of an event room with piano" style="left:704px;top:276px;width:168px;height:154px;background:radial-gradient(ellipse 70px 40px at 50% 20%,rgba(255,245,220,.8),transparent 70%),radial-gradient(ellipse 60px 30px at 40% 75%,rgba(40,35,30,.6),transparent 70%),linear-gradient(180deg,#d8c49a,#9a8258 60%,#6a5638)"></div>
  <div class="shot" role="img" aria-label="Photo of a banquet table setting" style="left:892px;top:276px;width:166px;height:154px;background:radial-gradient(ellipse 80px 30px at 50% 70%,rgba(250,250,250,.85),transparent 70%),radial-gradient(circle 25px at 30% 55%,rgba(240,200,120,.6),transparent 70%),linear-gradient(180deg,#c6d2de,#8a9aaa 60%,#6a7a88)"></div>
</section>
<h2 class="band" style="top:2847px">PHOTO <b>GALLERY</b></h2>

<footer class="site-footer">
  <h5 style="left:132px">CONTACT US</h5>
  <div class="foot-item" style="left:132px;top:60px"><i style="border-radius:50% 50% 50% 0"></i><span># 84 Wexbury Lane<br>Avon, MA 02417</span></div>
  <div class="foot-item" style="left:304px;top:60px"><i></i><span>(555) 014-2290</span></div>
  <div class="foot-item" style="left:304px;top:84px"><i></i><span>info@maplelanternco.example</span></div>
  <h5 style="left:530px">NEWSLETTER</h5>
  <div class="news-input">Email</div>
  <div class="news-btn">SUBSCRIBE</div>
  <h5 style="left:905px">FOLLOW US</h5>
  <div class="socials"><i></i><i></i><i></i><i></i></div>
</footer>
<div class="copyright">Copyright © 2017 maplelanternco.example all rights are reserved</div>

</body>
</html>
```